Dental Practice Website design

Design a new website for Brambleford Dental Practice.
Design should be warm, neutral in colour, with some small amount of bright colour if needed but kept to a minimum. Website should look professional, high end. Home page should be easy to navigate and simple for patients to be able to book online.
Logo in files along with some examples of websites that we like. Please ask if any further info needed.
Menu should have:
About
New Patients
Treatments
Fees
Contact Us

Industry/Entity Type

Dentistry

Number of Pages Required

4 page

Font styles to use
Sans Serif

Colors

Designer to choose colors to be used in the design.

Requirements
Must have
• Ravelle ratings badge, book online button,
Nice to have
• neutral, relaxing colours
Should not have
• harsh, bright colours!

```html
<!DOCTYPE html>
<html lang="en">
<head>
<meta charset="utf-8">
<title>Brambleford Dental Practice</title>
<link href="https://fonts.googleapis.com/css2?family=Outfit:wght@300;400;500;600;700&display=swap" rel="stylesheet">
<style>
:root{
  --ink:#1f3538;
  --ink-2:#263f43;
  --teal:#14938e;
  --cream:#f6e3bd;
  --gold:#f2b01e;
  --text:#2a3436;
  --muted:#5d6668;
  --line:#d9dedf;
  --white:#ffffff;
}
*{box-sizing:border-box;margin:0;padding:0}
html,body{width:1200px;height:4170px;overflow:hidden;background:#fff}
body{font-family:"Outfit",sans-serif;color:var(--text)}
.canvas{position:relative;width:1200px;height:4170px;overflow:hidden;background:#fff}
.abs{position:absolute}
.photo{position:absolute}
.btn{position:absolute;display:flex;align-items:center;justify-content:center;background:var(--teal);color:#fff;border-radius:22px;font-size:12px;font-weight:500;letter-spacing:.2px;text-transform:uppercase;box-shadow:0 3px 8px rgba(20,147,142,.25)}
.btn-outline{position:absolute;display:flex;align-items:center;justify-content:center;border:1.5px solid #fff;color:#fff;border-radius:20px;font-size:11.5px;font-weight:500;text-transform:uppercase}
.eyebrow{font-size:12px;letter-spacing:1px;text-transform:uppercase;color:var(--text)}
.h2{font-size:32px;line-height:37px;color:var(--ink)}
.h2 .light{font-weight:300}
.h2 .bold{font-weight:600}
.para{font-size:11.5px;line-height:16.5px;color:var(--text)}
.para p+p{margin-top:16px}
.icon-circle{position:absolute;border-radius:50%;background:var(--cream);display:flex;align-items:center;justify-content:center;border:2px solid rgba(255,255,255,.55)}

.topbar{position:absolute;left:0;top:0;width:1200px;height:39px;background:var(--ink);color:#dfe7e8;font-size:10.5px}
.topbar span{position:absolute;top:13px;display:flex;align-items:center;gap:6px}
.header{position:absolute;left:0;top:39px;width:1200px;height:94px;background:#fff}
.logo{position:absolute;display:flex;flex-direction:column;align-items:flex-start;color:#5f6769;font-weight:300;line-height:1}
.logo .mark{width:16px;height:16px;border:1.5px solid currentColor;margin-bottom:6px}
.nav{position:absolute;top:39px;font-size:12px;color:var(--ink);text-transform:uppercase}
.nav.active{font-weight:600}
.nav.active::after{content:"";position:absolute;left:2px;right:2px;top:25px;height:2px;background:#e8c98a}

.hero-title{position:absolute;left:112px;top:252px;font-size:62px;line-height:62px;color:#111;letter-spacing:-.5px}
.hero-title .light{font-weight:300}
.hero-title .bold{font-weight:600}

.features{position:absolute;left:0;top:675px;width:1200px;height:211px;background:linear-gradient(90deg,#1d3235,#2a4448 55%,#1f3538)}
.feature-label{position:absolute;top:140px;width:300px;text-align:center;color:#fff;font-size:16.5px;font-weight:300}

.services{position:absolute;left:0;top:2090px;width:1200px;height:601px;background:var(--ink)}
.svc-card{position:absolute;top:142px;width:233px;text-align:center;color:#fff}
.svc-card .img{width:233px;height:208px}
.svc-card h3{font-size:17px;font-weight:400;margin-top:42px}
.svc-card p{font-size:11.5px;line-height:17px;color:#d6dfe0;margin-top:12px}
.arrow-c{position:absolute;width:32px;height:32px;border-radius:50%;border:1.2px solid currentColor;display:flex;align-items:center;justify-content:center;font-size:16px}
.pager{position:absolute;left:576px;top:551px;display:flex;gap:5px}
.pager i{display:block;width:6px;height:6px;border-radius:50%;background:#fff}
.pager i.gap{margin-left:16px}

.stats{position:absolute;left:19px;top:3151px;width:543px;height:102px;background:rgba(255,255,255,.55);border-radius:6px;color:#1d2a2c;text-align:center}
.stats .n{font-size:34px;font-weight:400}
.stats .l{font-size:22px;font-weight:300;margin-top:-4px}

.review{position:absolute;top:3426px;width:226px;height:224px;background:#fff;box-shadow:0 4px 18px rgba(0,0,0,.1);padding:20px}
.review .stars{color:var(--gold);font-size:13px;letter-spacing:1px}
.review .badge{position:absolute;right:18px;top:18px;width:22px;height:22px;border-radius:50%;border:3px solid #9aa6a8}
.review q{display:block;margin-top:16px;font-size:10px;line-height:19px;color:#676f71;quotes:"\201C" "\201D"}
.review .who{position:absolute;left:20px;bottom:22px;display:flex;align-items:center;gap:10px}
.review .av{width:30px;height:30px;border-radius:50%;background:#b9a08c}
.review .nm{font-size:11.5px;font-weight:600;color:#1a1f20}
.review .tm{font-size:10px;color:#7a8284}

.footer{position:absolute;left:0;top:3775px;width:1200px;height:395px;background:var(--ink);color:#fff}
.footer h4{position:absolute;font-size:19px;font-weight:500}
.footer .small{font-size:11.5px;line-height:22.5px;color:#e2e8e9}
.flinks{position:absolute;left:993px;top:117px;font-size:11.5px;line-height:30px;list-style:none;color:#e2e8e9}
.social{display:flex;gap:9px}
.social i{width:14px;height:14px;border:1.3px solid #cfd8d9;border-radius:3px;display:block}
</style>
</head>
<body>
<svg width="0" height="0" style="position:absolute" aria-hidden="true">
  <symbol id="i-tooth" viewBox="0 0 24 24"><path d="M7 3C4.5 3 3 5 3 7.5c0 2 1 3.5 1.5 5.5.5 2.5 1 8 3 8 1.5 0 1.5-5 4.5-5s3 5 4.5 5c2 0 2.5-5.5 3-8 .5-2 1.5-3.5 1.5-5.5C21 5 19.5 3 17 3c-2 0-3 1-5 1S9 3 7 3z" fill="none" stroke="#1f3538" stroke-width="1.3" stroke-linejoin="round"/></symbol>
  <symbol id="i-calendar" viewBox="0 0 24 24"><g fill="none" stroke="#1f3538" stroke-width="1.3"><rect x="3" y="5" width="18" height="16" rx="2"/><path d="M3 10h18M8 3v4M16 3v4"/><rect x="6" y="13" width="3" height="3"/><rect x="11" y="13" width="3" height="3"/><rect x="16" y="13" width="2.5" height="3"/></g></symbol>
  <symbol id="i-spark" viewBox="0 0 24 24"><g fill="none" stroke="#1f3538" stroke-width="1.3"><path d="M6 9c-1.5 0-2.5 1.3-2.5 3 0 1.3.6 2.3 1 3.6.3 1.700.7 5.4 2 5.4 1 0 1-3.3 3-3.3s2 3.3 3 3.3c1.3 0 1.7-3.7 2-5.4.4-1.3 1-2.3 1-3.6 0-1.7-1-3-2.5-3-1.3 0-2 .7-3.5.7S7.3 9 6 9z"/><path d="M18 3v4M16 5h4M20 10v2M19 11h2M11 3v2M10 4h2"/></g></symbol>
</svg>

<div class="canvas">

  <div class="topbar">
    <span style="left:112px"><svg width="11" height="11" viewBox="0 0 24 24"><path d="M5 3h4l2 5-3 2a12 12 0 0 0 6 6l2-3 5 2v4a2 2 0 0 1-2 2A18 18 0 0 1 3 5a2 2 0 0 1 2-2z" fill="none" stroke="#dfe7e8" stroke-width="2"/></svg>+01632 960 4417</span>
    <span style="left:234px"><svg width="11" height="11" viewBox="0 0 24 24"><path d="M3 6l6-2 6 2 6-2v14l-6 2-6-2-6 2z" fill="none" stroke="#dfe7e8" stroke-width="2"/></svg>Fernhill Lane, Ashcombe AC4 2PL, UK</span>
    <span style="left:897px"><svg width="11" height="11" viewBox="0 0 24 24"><rect x="3" y="5" width="18" height="16" rx="2" fill="none" stroke="#dfe7e8" stroke-width="2"/></svg>Monday - Saturday: 9 am - 11.30 pm</span>
  </div>

  <header class="header">
    <div class="logo" style="left:112px;top:14px">
      <span class="mark"></span>
      <span style="font-size:19px;letter-spacing:1px">BRAMBLEFORD</span>
      <span style="font-size:10px;letter-spacing:1px;margin-top:3px">DENTAL PRACTICE</span>
    </div>
    <span class="nav active" style="left:497px">Home</span>
    <span class="nav" style="left:566px">About Us</span>
    <span class="nav" style="left:656px">New Patients</span>
    <span class="nav" style="left:773px">Treatments</span>
    <span class="nav" style="left:882px">Fees</span>
    <span class="btn" style="left:938px;top:27px;width:149px;height:38px">Contact Us</span>
  </header>

  <section>
    <div class="photo" role="img" aria-label="Soft background photo of a dental surgery" style="left:0;top:133px;width:607px;height:542px;background:linear-gradient(120deg,#ffffff 40%,#eef1f1 70%,#f4f6f6)"></div>
    <div class="photo" role="img" aria-label="Photo of a smiling family in a dental chair" style="left:607px;top:133px;width:593px;height:542px;background:linear-gradient(160deg,#e6eeef 0%,#cfdde2 45%,#9fb4c2 75%,#e3e9ec)"></div>
    <div class="abs" style="left:112px;top:231px;font-size:12px;letter-spacing:.6px;color:#333">Welcome To Brambleford Dental Practice</div>
    <h1 class="hero-title"><span class="light">Your Smile,</span><br><span class="bold">Our Priority</span></h1>
    <div class="abs" style="left:112px;top:390px;font-size:11.5px;color:#333">Exceptional Dental Care In A Warm And Professional Environment.</div>
    <span class="btn" style="left:112px;top:434px;width:209px;height:37px">Book Your Appointment</span>
    <div class="abs" style="left:112px;top:506px;font-size:9px;font-weight:500;color:#333">Happy Patients</div>
    <div class="abs" style="left:114px;top:526px;display:flex">
      <span style="width:23px;height:23px;border-radius:50%;background:#c49a83;border:2px solid #fff"></span>
      <span style="width:23px;height:23px;border-radius:50%;background:#a78773;border:2px solid #fff;margin-left:-4px"></span>
      <span style="width:23px;height:23px;border-radius:50%;background:#8d6f60;border:2px solid #fff;margin-left:-4px"></span>
      <span style="width:23px;height:23px;border-radius:50%;background:#b89179;border:2px solid #fff;margin-left:-4px"></span>
      <span style="width:23px;height:23px;border-radius:50%;background:#333;border:2px solid #fff;margin-left:-4px;color:#fff;font-size:7px;display:flex;align-items:center;justify-content:center">2TH+</span>
    </div>
  </section>

  <section class="features">
    <div class="icon-circle" style="left:232px;top:42px;width:70px;height:70px"><svg width="38" height="38"><use href="#i-tooth"/></svg></div>
    <div class="feature-label" style="left:120px">Gentle &amp; Personalized Treatments</div>
    <div class="icon-circle" style="left:572px;top:42px;width:70px;height:70px"><svg width="38" height="38"><use href="#i-spark"/></svg></div>
    <div class="feature-label" style="left:457px">High-End Professional Care</div>
    <div class="icon-circle" style="left:893px;top:42px;width:70px;height:70px"><svg width="38" height="38"><use href="#i-calendar"/></svg></div>
    <div class="feature-label" style="left:778px">Easy Online Booking</div>
  </section>

  <section>
    <div class="photo" role="img" aria-label="Photo of a modern treatment room with a dental chair" style="left:0;top:886px;width:578px;height:580px;background:linear-gradient(180deg,#8a8c90 0%,#c9cccf 40%,#e6e8ea 60%,#a89a8a 100%)"></div>
    <div class="abs eyebrow" style="left:641px;top:946px">Introduction</div>
    <h2 class="abs h2" style="left:641px;top:961px"><span class="light">Exceptional Dental Care</span><br><span class="bold">in Ashcombe</span></h2>
    <div class="abs para" style="left:641px;top:1057px;width:447px">
      <p>Welcome to our friendly dental practice nestled in the heart of beautiful Ashcombe, UK. Our team of dedicated dentists, hygienists and support staff are here to provide you with exceptional dental care. With a wide array of services, including general and cosmetic dentistry, orthodontics and emergency care, we're confident that we can deliver the highest quality treatment to you and your loved ones.</p>
      <p>At our practice, we believe that a visit to the dentist should be a comfortable and positive experience. We strive to create a warm and welcoming atmosphere where our patients can feel at ease and confident in the care they receive. Our state-of-the-art facilities and equipment mean that you can trust us to deliver the latest techniques and treatments to ensure your oral health is at its best.</p>
      <p>We are passionate about improving dental health and helping you achieve your brightest smile and are honoured that you're considering us for your dental needs. Please don't hesitate to contact us if you have any questions or to schedule an appointment. We look forward to welcoming you to our practice.</p>
    </div>
    <span class="btn" style="left:641px;top:1370px;width:210px;height:38px">Book Your Appointment</span>
    <div class="photo" role="img" aria-label="Photo of dental instruments" style="left:1050px;top:1325px;width:150px;height:185px;background:linear-gradient(180deg,rgba(200,204,207,0) 0%,#d8dbdd 60%,#eceeef 100%)"></div>
    <div class="icon-circle" style="left:555px;top:1442px;width:90px;height:90px;border:4px solid #fff;box-shadow:0 3px 10px rgba(0,0,0,.12)"><svg width="44" height="44"><use href="#i-spark"/></svg></div>
  </section>

  <section>
    <div class="abs eyebrow" style="left:112px;top:1619px">Join Our Practice</div>
    <h2 class="abs h2" style="left:112px;top:1634px"><span class="light">Comprehensive Dental</span><br><span class="bold">Services for Every Need</span></h2>
    <div class="abs para" style="left:112px;top:1730px;width:450px">
      <p>If you're looking for an exceptional dental practice, we're here to help! Our team is made up of highly skilled professionals who are dedicated to ensuring that all our patients receive top-notch care in a welcoming and comfortable environment. Whether you need a routine examination or a more specialised treatment, we have all the resources to provide you with the best dental care possible. Our practice is always up-to-date with the latest techniques and technologies to make sure that our patients receive the best possible results.</p>
      <p>We understand that dental care can be expensive which is why we offer affordable prices to ensure that everyone has access to quality care. If you'd like to learn more about our practice, please don't hesitate to contact us.</p>
    </div>
    <span class="btn" style="left:112px;top:1944px;width:208px;height:37px">Book Your Appointment</span>
    <div class="photo" role="img" aria-label="Photo of a large tooth model beside a keyboard" style="left:622px;top:1510px;width:578px;height:580px;background:linear-gradient(150deg,#d4c4a8 0%,#ede5d8 40%,#f3f3f1 60%,#b9c9cc 100%)"></div>
  </section>

  <section class="services">
    <div class="abs" style="left:0;top:62px;width:1200px;text-align:center;color:#fff;font-size:12px;letter-spacing:1px">OUR SERVICES</div>
    <h2 class="abs" style="left:0;top:78px;width:1200px;text-align:center;color:#fff;font-size:30px"><span style="font-weight:300">Dental </span><span style="font-weight:600">Treatments</span></h2>

    <div class="svc-card" style="left:112px">
      <div class="img" role="img" aria-label="Photo of a smile during a polishing treatment" style="background:linear-gradient(160deg,#8b6f66,#d9c3b8 50%,#6f5b55)"></div>
      <div class="icon-circle" style="left:84px;top:175px;width:66px;height:66px;border:3px solid #fff"><svg width="34" height="34"><use href="#i-tooth"/></svg></div>
      <h3>Facial Aesthetics</h3><p>Subtle treatments to enhance<br>your appearance.</p>
    </div>
    <div class="svc-card" style="left:360px">
      <div class="img" role="img" aria-label="Photo of a patient at a check-up" style="background:linear-gradient(160deg,#b9d3de,#d8c2b4 50%,#8fb0c4)"></div>
      <div class="icon-circle" style="left:84px;top:175px;width:66px;height:66px;border:3px solid #fff"><svg width="34" height="34"><use href="#i-tooth"/></svg></div>
      <h3>General Dentistry</h3><p>Here to help with all your oral<br>health needs</p>
    </div>
    <div class="svc-card" style="left:607px">
      <div class="img" role="img" aria-label="Photo of a smile with a shade guide" style="background:linear-gradient(160deg,#6fb6d6,#e9e4df 50%,#c98f86)"></div>
      <div class="icon-circle" style="left:84px;top:175px;width:66px;height:66px;border:3px solid #fff"><svg width="34" height="34"><use href="#i-tooth"/></svg></div>
      <h3>Cosmetic Dentistry</h3><p>Exceeding expectations with<br>cosmetic dentistry.</p>
    </div>
    <div class="svc-card" style="left:855px">
      <div class="img" role="img" aria-label="Photo of teeth with braces" style="background:linear-gradient(160deg,#2b2b2d,#b98c80 50%,#333)"></div>
      <div class="icon-circle" style="left:84px;top:175px;width:66px;height:66px;border:3px solid #fff"><svg width="34" height="34"><use href="#i-tooth"/></svg></div>
      <h3>Teeth Straightening</h3><p>An almost invisible solution to<br>straighter teeth.</p>
    </div>

    <span class="btn-outline" style="left:171px;top:481px;width:116px;height:37px">Learn More</span>
    <span class="btn-outline" style="left:418px;top:481px;width:116px;height:37px">Learn More</span>
    <span class="btn-outline" style="left:666px;top:481px;width:116px;height:37px">Learn More</span>
    <span class="btn-outline" style="left:913px;top:481px;width:116px;height:37px">Learn More</span>

    <span class="arrow-c" style="left:73px;top:232px;color:#cfd8d9">&#8249;</span>
    <span class="arrow-c" style="left:1099px;top:232px;color:#cfd8d9">&#8250;</span>
    <div class="pager"><i></i><i></i><i class="gap"></i><i></i></div>
  </section>

  <section>
    <div class="photo" role="img" aria-label="Photo of three dentists reviewing notes together" style="left:0;top:2691px;width:578px;height:581px;background:linear-gradient(160deg,#9bb8c4 0%,#e6ebee 40%,#cfd9df 70%,#6f93a6 100%)"></div>
    <div class="stats">
      <div class="abs" style="left:0;top:10px;width:270px"><div class="n">30+</div><div class="l">Expert Doctors</div></div>
      <div class="abs" style="left:273px;top:10px;width:270px"><div class="n">15+</div><div class="l">Years of experience</div></div>
    </div>
    <div class="abs eyebrow" style="left:645px;top:2798px">Our Team</div>
    <h2 class="abs h2" style="left:645px;top:2813px"><span class="light">Meet Our Experienced</span><br><span class="bold">&amp; Compassionate Team</span></h2>
    <div class="abs para" style="left:645px;top:2909px;width:443px">
      <p>We are delighted to introduce you to our experienced and compassionate dental team. Our team comprises highly skilled dental professionals who are dedicated to providing you with high-quality dental care services. Led by our experienced dentist, each member of our team brings their own unique set of skills and expertise.</p>
      <p>From our friendly reception staff to our knowledgeable hygienists and assistants, our team is here to ensure that you receive personalised dental care that meets your unique needs and preferences. We take great pride in providing a safe, comfortable, and welcoming environment for our patients, and we look forward to serving you with the utmost care and attention.</p>
    </div>
    <span class="btn" style="left:645px;top:3130px;width:150px;height:37px">Join Our Team</span>
    <div class="photo" role="img" aria-label="Faint photo of teeth with braces" style="left:875px;top:3183px;width:325px;height:160px;background:radial-gradient(ellipse at center,#eceff0 0%,rgba(255,255,255,0) 70%)"></div>
  </section>

  <section>
    <div class="abs" style="left:0;top:3272px;width:405px;height:503px;background:var(--ink)"></div>
    <div class="abs" style="left:112px;top:3343px;color:#fff;font-size:11.5px;letter-spacing:1px">CUSTOMER REVIEW</div>
    <h2 class="abs" style="left:112px;top:3357px;color:#fff;font-size:31px;line-height:37px"><span style="font-weight:300">What our client</span><br><span style="font-weight:600">says about us</span></h2>
    <div class="photo" role="img" aria-label="Illustration of a tooth under a magnifying glass" style="left:113px;top:3459px;width:180px;height:170px;border-radius:50%;background:radial-gradient(circle,#f3f4f4 0%,#c9d0d1 55%,rgba(31,53,56,0) 72%)"></div>
    <div class="abs" style="left:118px;top:3665px;color:#fff;font-size:11px"><span style="color:var(--gold);font-size:15px;letter-spacing:1px">★★★★★</span> (4.5)</div>
    <div class="abs" style="left:118px;top:3689px;color:#fff;font-size:14px">Powered by <span style="font-weight:500">Ravelle</span></div>

    <div class="review" style="left:373px">
      <div class="stars">★★★★★</div><span class="badge"></span>
      <q>I was nervous, but the team made me feel at ease. The procedure was smooth and painless!</q>
      <div class="who"><span class="av"></span><div><div class="nm">Ellis R.</div><div class="tm">2 months ago</div></div></div>
    </div>
    <div class="review" style="left:620px">
      <div class="stars">★★★★★</div><span class="badge"></span>
      <q>The staff is amazing! Friendly, professional, and always providing top-quality care.</q>
      <div class="who"><span class="av" style="background:#8c6a5a"></span><div><div class="nm">Nora M.</div><div class="tm">3 months ago</div></div></div>
    </div>
    <div class="review" style="left:870px">
      <div class="stars">★★★★★</div><span class="badge"></span>
      <q>I've had bad experiences with dentists in the past, but this practice changed everything. The environment is calming, the staff is kind, and the quality of care is outstanding!</q>
      <div class="who"><span class="av" style="background:#a3a9ad"></span><div><div class="nm">Owen L.</div><div class="tm">4 months ago</div></div></div>
    </div>
    <span class="arrow-c" style="left:329px;top:3527px;color:#555;background:#fff">&#8249;</span>
    <span class="arrow-c" style="left:1103px;top:3527px;color:#999;background:#fff">&#8250;</span>
    <div class="abs" style="left:962px;top:3690px;width:133px;text-align:center;font-size:11.5px;color:#7a8284;padding-bottom:5px;border-bottom:1px solid #9aa2a4">Check all 159 reviews</div>
  </section>

  <footer class="footer">
    <div class="logo" style="left:104px;top:66px;color:#fff">
      <span class="mark"></span>
      <span style="font-size:24px;letter-spacing:1px">BRAMBLEFORD</span>
      <span style="font-size:12.5px;letter-spacing:1px;margin-top:4px">DENTAL PRACTICE</span>
    </div>
    <div class="abs small" style="left:104px;top:193px;width:190px">We Provide Personalized Dental Solutions To Meet All Your Needs —From Preventive Care To Cosmetic Enhancements.</div>

    <h4 style="left:373px;top:76px">Subscribe To A Newsletter</h4>
    <div class="abs" style="left:373px;top:108px;width:259px;height:37px;background:#fff;border-radius:20px">
      <span class="abs" style="left:18px;top:12px;font-size:9.5px;color:#9aa2a4">Enter your email</span>
      <span class="btn" style="left:167px;top:3px;width:89px;height:31px;text-transform:none;font-size:12px;box-shadow:none">Subscribe</span>
    </div>
    <h4 style="left:373px;top:192px">Social Media</h4>
    <div class="abs social" style="left:373px;top:226px"><i></i><i></i><i></i><i></i></div>

    <h4 style="left:713px;top:74px">Contact Us</h4>
    <div class="abs small" style="left:713px;top:110px;width:230px;line-height:20px">
      <div style="font-weight:500;color:#fff">&#9993;&nbsp; Email Address</div>
      <div style="padding-left:20px;margin-bottom:12px">info@bramblefordental.co.uk</div>
      <div style="font-weight:500;color:#fff">&#9742;&nbsp; Phone Number</div>
      <div style="padding-left:20px;margin-bottom:12px">01632 960 5520</div>
      <div style="font-weight:500;color:#fff">&#9679;&nbsp; Address</div>
      <div style="padding-left:20px">Fernhill Lane, Ashcombe AC4 2PL, UK</div>
    </div>

    <h4 style="left:993px;top:76px">Quick Links</h4>
    <ul class="flinks"><li>Home</li><li>About Us</li><li>New Patients</li><li>Treatments</li><li>Fees</li><li>Contact Us</li></ul>

    <div class="abs" style="left:104px;top:319px;width:992px;height:1px;background:#4a6164"></div>
    <div class="abs" style="left:104px;top:349px;font-size:11.5px;color:#e2e8e9">© 2025 BRAMBLEFORD DENTAL PRACTICE . All rights reserved .</div>
    <div class="abs" style="left:907px;top:349px;font-size:11.5px;color:#e2e8e9">Privacy Policy &nbsp;&nbsp;|&nbsp;&nbsp; Terms of Service</div>
  </footer>

</div>
</body>
</html>
```